Business Card Design Project

This is to go hand in hand with our stationery project.
Target Market(s)
Business Professionals in the Finance, HR and C-Level management arena. They are global companies that run enterprise technology solutions/products.
Mostly Male, mid 30's to 60's.
Industry/Entity Type
Business
Font styles to use
Other font styles liked:
- Calibri
Colors
9bcb3c
000000
1b1b1b
c4c4c4
ffffff
Requirements
Must have
- Logo
Name, title, contact details, address on the front of the card.
ABN and web address need to be on the card, along with our tag line
See | Share | Do
We also require rounded corners and for the card to be landscape please.
Our green is
C98 M0 Y93 K0
Modern, contemporary and must have white space for people to write on.
Nice to have
- Consistent elements with the stationery design.
Should not have
- No 90's waves - We want the feeling of movement but no wavey lines.

```html
<!DOCTYPE html>
<html lang="en">
<head>
<meta charset="utf-8">
<title>Kestrel Business Solutions – Business Cards</title>
<link rel="stylesheet" href="https://fonts.googleapis.com/css2?family=Open+Sans:wght@400;600;700&display=swap">
<style>
  :root {
    --green: #9bcb3c;
    --black: #000000;
    --charcoal: #1b1b1b;
    --charcoal-soft: #262626;
    --ghost: #333333;
    --grey: #c4c4c4;
    --white: #ffffff;
    --stage: #e9e9e9;
    --ink: #1b1b1b;
  }
  * { box-sizing: border-box; margin: 0; padding: 0; }
  html, body { width: 1200px; height: 914px; overflow: hidden; }
  body {
    background: var(--stage);
    font-family: "Open Sans", "Carlito", sans-serif;
    display: flex;
    align-items: center;
    justify-content: center;
    gap: 40px;
  }
  .card {
    position: relative;
    width: 540px;
    height: 330px;
    border-radius: 14px;
    overflow: hidden;
    box-shadow: 0 6px 20px rgba(0,0,0,0.18);
  }

  /* Front: dark card */
  .card--front {
    background: linear-gradient(160deg, var(--charcoal-soft), var(--charcoal));
    color: var(--white);
  }
  .front__title {
    position: absolute;
    top: 34px; left: 34px;
    font-size: 31px;
    font-weight: 700;
    letter-spacing: 0.3px;
    white-space: nowrap;
  }
  .front__ghost {
    position: absolute;
    right: 28px; top: 150px;
    font-size: 52px;
    font-weight: 700;
    color: var(--ghost);
    line-height: 1;
    white-space: nowrap;
  }
  .front__details {
    position: absolute;
    top: 102px; left: 34px;
    width: 230px;
    font-size: 13px;
    line-height: 1.55;
    list-style: none;
  }
  .front__abn { margin-bottom: 6px; }
  .detail { display: flex; align-items: center; gap: 8px; white-space: nowrap; }
  .detail svg { width: 13px; height: 13px; flex: none; fill: var(--green); }
  .detail--address { margin-top: 4px; }
  .front__band {
    position: absolute;
    left: 0; right: 0; bottom: 0;
    height: 34px;
    display: flex;
  }
  .band__grey {
    width: 45%;
    background: var(--grey);
    border-top: 5px solid var(--green);
  }
  .band__green { flex: 1; background: var(--green); }

  /* Back: white card */
  .card--back {
    background: var(--white);
    color: var(--ink);
    display: flex;
    flex-direction: column;
    align-items: center;
    justify-content: center;
  }
  .back__name {
    display: flex;
    align-items: center;
    gap: 12px;
    font-size: 30px;
    font-weight: 700;
    white-space: nowrap;
  }
  .back__dot {
    width: 16px; height: 16px;
    border-radius: 50%;
    background: var(--green);
  }
  .back__tagline {
    margin-top: 22px;
    font-size: 24px;
    font-weight: 400;
    display: flex;
    align-items: center;
    gap: 12px;
  }
  .tagline__sep {
    width: 1px; height: 20px;
    background: var(--grey);
  }
  .back__abn {
    margin-top: 8px;
    font-size: 15px;
  }
</style>
</head>
<body>

  <section class="card card--front" aria-label="Business card front">
    <h1 class="front__title">Kestrel Business Solutions</h1>
    <div class="front__ghost" aria-hidden="true">Kestrel</div>
    <ul class="front__details">
      <li class="front__abn">ABN: 12 345678 901</li>
      <li class="detail">
        <svg viewBox="0 0 16 16" aria-hidden="true"><circle cx="8" cy="5" r="3.5"/><path d="M1 16c0-4 3-6 7-6s7 2 7 6z"/></svg>
        +61 2 9000 1234
      </li>
      <li class="detail">
        <svg viewBox="0 0 16 16" aria-hidden="true"><rect x="4" y="1" width="8" height="4"/><rect x="1" y="6" width="14" height="6" rx="1"/><rect x="4" y="10" width="8" height="5"/></svg>
        +61 2 90005678
      </li>
      <li class="detail">
        <svg viewBox="0 0 16 16" aria-hidden="true"><path d="M1 3h14v10H1z M1 3l7 6 7-6" stroke="#1b1b1b" stroke-width="1"/></svg>
        sales@kestrelbiz.com
      </li>
      <li class="detail">
        <svg viewBox="0 0 16 16" aria-hidden="true"><circle cx="8" cy="8" r="7"/><path d="M1 8h14M8 1c-3 4-3 10 0 14M8 1c3 4 3 10 0 14" stroke="#1b1b1b" stroke-width="1" fill="none"/></svg>
        www.kestrelbiz.com
      </li>
      <li class="detail--address">Level 2, 18 Harbour Lane,<br>Eastwood, NSW 2000</li>
    </ul>
    <div class="front__band" aria-hidden="true">
      <div class="band__grey"></div>
      <div class="band__green"></div>
    </div>
  </section>

  <section class="card card--back" aria-label="Business card back">
    <div class="back__name">
      <span class="back__dot" aria-hidden="true"></span>
      Kestrel Business Solutions
    </div>
    <p class="back__tagline">
      Plan <span class="tagline__sep" aria-hidden="true"></span>
      Build <span class="tagline__sep" aria-hidden="true"></span>
      Grow
    </p>
    <p class="back__abn">ABN: 12 345678 901</p>
  </section>

</body>
</html>
```